Design and Renovation Company Luxury Business Card

I want to create a luxury business card for a Design and Renovation Firm . We will use our current logo. The company name is 528BUILDA. We do not want anything standard. We need a very unique concept.
Please see uploaded inspiration. I really like the textured paper option. I would like the card to be thick with debossing, and/or embossing options. The logo has orange in it but I would like to see the card with and without the orange. I think the orange may make the company feel less high-end. The goal is to elevate the logo not match its vibe per se of the logo. We want something very unique, not standard at all!
I would like a space for :
Logo,
Name,
Position,
Email,
Office number,
Website Address,
Business Address,
Thank you!
Have fun!
Target Market(s)
Home owners Age 35 +
Industry/Entity Type
Design and Renovation
Contact Information for Business Card
Logo, Name, Position, Email, Office number, Website Address, Business Address,.
Colors
Designer to choose colors to be used in the design.
Requirements
Must have
- A luxury designer feel. Must be black or dark grey but open to other luxury ideas.
Nice to have
- Gold, silver, black embossing or debossing. Textured paper design.
Should not have
- A cheap look and feel.

```html
<!DOCTYPE html>
<html lang="en">
<head>
<meta charset="UTF-8">
<title>528BUILDA Business Card</title>
<link href="https://fonts.googleapis.com/css2?family=Roboto:wght@300;400;700&display=swap" rel="stylesheet">
<style>
  :root {
    --backdrop: #1b1b1b;
    --card: #3b3b3c;
    --card-edge: #343435;
    --deboss: #303031;
    --ink: #050505;
    --ink-soft: #151515;
  }
  * { box-sizing: border-box; margin: 0; padding: 0; }
  html, body {
    width: 1200px; height: 1015px; overflow: hidden;
    background: radial-gradient(ellipse at 50% 45%, #2a2a2a 0%, var(--backdrop) 70%);
    font-family: "Roboto", sans-serif;
  }
  .stage {
    width: 1200px; height: 1015px;
    display: flex; flex-direction: column; align-items: center; justify-content: center; gap: 56px;
  }
  .card {
    position: relative; width: 700px; height: 400px;
    background: linear-gradient(160deg, #404041 0%, var(--card) 55%, var(--card-edge) 100%);
    box-shadow: 0 18px 40px rgba(0,0,0,.55);
  }

  /* Front: quiet debossed name */
  .card--front { display: flex; align-items: center; justify-content: center; }
  .front-name {
    font-weight: 300; font-size: 64px; letter-spacing: 4px; line-height: 1;
    color: var(--deboss);
  }

  /* Back: details */
  .card--back { padding: 70px 60px 0 70px; }
  .brand-name {
    font-size: 74px; font-weight: 400; letter-spacing: 5px; line-height: 1;
    color: var(--ink); text-align: center;
  }
  .details { display: flex; align-items: stretch; justify-content: center; margin-top: 52px; }
  .person { text-align: right; align-self: flex-end; padding-right: 22px; }
  .person__name { font-size: 27px; font-weight: 700; letter-spacing: 1px; color: var(--ink); line-height: 1.1; }
  .person__role { font-size: 20px; font-weight: 400; color: var(--ink-soft); }
  .divider { width: 1.5px; background: var(--ink); }
  .contacts { list-style: none; padding-left: 18px; }
  .contacts li {
    display: flex; align-items: center; gap: 8px;
    font-size: 20px; color: var(--ink); line-height: 1.35;
  }
  .contacts svg { width: 18px; height: 18px; flex: none; }
  .address { font-size: 20px; color: var(--ink); margin-top: 44px; text-align: center; }
</style>
</head>
<body>
<main class="stage">
  <section class="card card--front" aria-label="Card front">
    <div class="front-name">528BUILDA</div>
  </section>

  <section class="card card--back" aria-label="Card back">
    <div class="brand-name">528BUILDA</div>

    <div class="details">
      <div class="person">
        <div class="person__name">MARCUS HALE</div>
        <div class="person__role">Managing Director</div>
      </div>
      <span class="divider"></span>
      <ul class="contacts">
        <li>
          <svg viewBox="0 0 20 20" aria-hidden="true"><circle cx="10" cy="10" r="9" fill="none" stroke="#050505" stroke-width="2"/><path d="M7 6l2 2-1 1.5c.7 1.4 1.6 2.3 3 3L12.5 11l2 2-1.5 1.5C9.5 14 6 10.5 5.5 6.5z" fill="#050505"/></svg>
          044-987 654 321
        </li>
        <li>
          <svg viewBox="0 0 20 20" aria-hidden="true"><rect x="1" y="4" width="18" height="12" fill="#050505"/><path d="M1 4l9 7 9-7" fill="none" stroke="#3b3b3c" stroke-width="1.5"/></svg>
          hello@studiomail.com
        </li>
        <li>
          <svg viewBox="0 0 20 20" aria-hidden="true"><circle cx="10" cy="10" r="9" fill="#050505"/><path d="M1 10h18M10 1c-4 4-4 14 0 18M10 1c4 4 4 14 0 18" fill="none" stroke="#3b3b3c" stroke-width="1.2"/></svg>
          www.studiosite.com
        </li>
      </ul>
    </div>

    <p class="address">87, Street line here 30719, Region Name</p>
  </section>
</main>
</body>
</html>
```